Harbor Crestline (Business Card Design)

Need business cards designed. Something modern, chic, and sleek. Mabye the back of the card should be the navy blue that is in the logo and then just the logo on the back.

Target Market(s)

Those in the hotel, office, and renovation industry

Contact Information for Business Card

1. Logo 2. Dorian Fenwick 3. CEO/Founder 4. Phone: (833) HarbCre / (833) 427-2731 5. Email: dorian@theharborcrestline.com 6. Website: www.theharborcrestline.com

Font styles to use
Other font styles liked:
• Look at the logo font and base the font for everything else off of that.

Colors
0054AA
0677BA
7BADD7
CADEEF
E8F1F8

Requirements
Must have
• Colors that are associated in the logo
Nice to have
• Sleek modern clean and chic design.

```html
<!DOCTYPE html>
<html lang="en">
<head>
<meta charset="utf-8">
<title>Harbor Crestline – Business Card</title>
<link rel="stylesheet" href="https://fonts.googleapis.com/css2?family=Bebas+Neue&family=Montserrat:wght@600&family=Poppins:wght@400&display=swap">
<style>
  :root {
    --backdrop: #8c8c8c;
    --card-white: #ffffff;
    --navy: #111a3e;
    --name-navy: #151d42;
    --gold: #c99a34;
    --text-gray: #6b6b6b;
  }
  * { margin: 0; padding: 0; box-sizing: border-box; }
  html, body {
    width: 1200px;
    height: 959px;
    overflow: hidden;
  }
  body {
    position: relative;
    background: var(--backdrop);
  }
  .card {
    position: absolute;
    left: 295px;
    width: 612px;
    height: 351px;
    box-shadow: 0 3px 10px rgba(0, 0, 0, 0.25);
  }
  .card-front { top: 103px; background: var(--card-white); }
  .card-back  { top: 499px; background: var(--navy); }

  /* Front */
  .identity {
    position: absolute;
    right: 377px; /* right edge at x=530 on the page */
    top: 145px;
    text-align: right;
  }
  .identity-name {
    font-family: "Bebas Neue", sans-serif;
    font-size: 38px;
    line-height: 38px;
    color: var(--name-navy);
    letter-spacing: 0.3px;
    white-space: nowrap;
  }
  .identity-title {
    font-family: "Poppins", sans-serif;
    font-size: 15.5px;
    line-height: 18px;
    color: var(--gold);
    margin-top: 1px;
  }
  .divider {
    position: absolute;
    left: 252px;
    top: 147px;
    width: 2px;
    height: 57px;
    background: var(--gold);
  }
  .contact-list {
    position: absolute;
    left: 269px;
    top: 145px;
    list-style: none;
  }
  .contact-item {
    display: flex;
    align-items: center;
    height: 22px;
    font-family: "Poppins", sans-serif;
    font-size: 15px;
    color: var(--text-gray);
    white-space: nowrap;
  }
  .contact-icon {
    width: 13px;
    height: 13px;
    margin-right: 3px;
    fill: var(--name-navy);
    flex: none;
  }

  /* Back */
  .wordmark {
    position: absolute;
    left: 0;
    right: 0;
    top: 148px;
    text-align: center;
    font-family: "Montserrat", sans-serif;
    font-weight: 600;
    color: var(--card-white);
  }
  .wordmark-main {
    font-size: 29px;
    line-height: 32px;
    letter-spacing: 2px;
  }
  .wordmark-sub {
    font-size: 10px;
    line-height: 14px;
    letter-spacing: 6.5px;
    margin-top: 2px;
  }
</style>
</head>
<body>
  <section class="card card-front">
    <div class="identity">
      <h1 class="identity-name">DORIAN FENWICK</h1>
      <p class="identity-title">CEO/Founder</p>
    </div>
    <div class="divider"></div>
    <ul class="contact-list">
      <li class="contact-item">
        <svg class="contact-icon" viewBox="0 0 24 24" aria-hidden="true"><path d="M6.6 10.8c1.4 2.8 3.8 5.1 6.6 6.6l2.2-2.2c.3-.3.7-.4 1-.2 1.1.4 2.3.6 3.6.6.6 0 1 .4 1 1V20c0 .6-.4 1-1 1C10.6 21 3 13.4 3 4c0-.6.4-1 1-1h3.5c.6 0 1 .4 1 1 0 1.3.2 2.5.6 3.6.1.3 0 .7-.2 1l-2.3 2.2z"/></svg>
        (833) HarbCre / (833) 427-2731 5
      </li>
      <li class="contact-item">
        <svg class="contact-icon" viewBox="0 0 24 24" aria-hidden="true"><path d="M2 5h20v14H2z M2 5l10 8 10-8" fill="none" stroke="#151d42" stroke-width="0"/><path d="M2 5h20L12 12.5z M2 7.2l6.3 5L2 17.5z M22 7.2l-6.3 5 6.3 5.3z M9.6 13.2L12 15l2.4-1.8L22 19H2z"/></svg>
        dorian@theharborcrestline.com
      </li>
      <li class="contact-item">
        <svg class="contact-icon" viewBox="0 0 24 24" aria-hidden="true"><circle cx="12" cy="12" r="9.5" fill="none" stroke="#151d42" stroke-width="1.8"/><ellipse cx="12" cy="12" rx="4" ry="9.5" fill="none" stroke="#151d42" stroke-width="1.6"/><path d="M2.5 12h19M4 7.5h16M4 16.5h16" stroke="#151d42" stroke-width="1.5"/></svg>
        www.theharborcrestline.com
      </li>
    </ul>
  </section>

  <section class="card card-back">
    <div class="wordmark">
      <p class="wordmark-main">HARBOR</p>
      <p class="wordmark-sub">CRESTLINE</p>
    </div>
  </section>
</body>
</html>
```